zorvan lumet website design

An IT support and IT Security Company - just use dummy text for now for the design. Examples of sites we like the looks and feel of but need it more professional feel are like: www.kelbrovault.uk.com , www.pravok.co.uk, www.quenthardy.com/professional/, www.vur.com, www.melvish.com,

Best to message me if you have any questions

Target Market(s)

small to medium UK based companies that require IT support services

Industry/Entity Type

It Company

Contact Information for Business Card

use dummy name, telephone and email for now, will provide details later.

Logo Text

zorvan lumet (and then below the logo it should say "your IT, networks and security partner")

Coding

Coded - Design and coding required

Number of Pages Required

5+ page

Colors

Designer to choose colors to be used in the design.

Requirements
Must have
• must be professional, yet simple and clear that this is a serious IT support and IT security company.
Nice to have
• 1)The website homepage must have professional quality pictures of IT support or London city skyline or any picture that projects friendly business partners, professionalism and ready to serve.
• 2) Home page needs to include tabs for following pages 'Services' , 'About Us' , 'Contact Us' 'Home'
• 3) Website built customised using wordpress is ideal and easy for us to manage.
• more room for boxed options from homepage (with pic or image in background)
Should not have
• no checkout trolleys or payment options.

```html
<!DOCTYPE html>
<html lang="en">
<head>
<meta charset="utf-8">
<title>Zorvan Lumet – IT Support and IT Security</title>
<link href="https://fonts.googleapis.com/css2?family=Raleway:wght@500;600;700;800&family=Open+Sans:wght@400;600;700&display=swap" rel="stylesheet">
<style>
:root{
  --red:#a8151c;
  --red-dark:#8e1016;
  --ink:#1c1c1c;
  --charcoal:#333333;
  --dark:#1f2124;
  --footer:#2b2b2b;
  --grey:#777777;
  --light-grey:#b5b5b5;
  --white:#ffffff;
  --head:'Raleway',sans-serif;
  --body:'Open Sans',sans-serif;
}
*{box-sizing:border-box;margin:0;padding:0}
html,body{width:1200px;height:3442px;overflow:hidden}
body{font-family:var(--body);color:var(--grey);background:var(--white);position:relative}
section,header,footer,.topbar{position:relative;width:1200px;overflow:hidden}
.wrap{width:1044px;margin:0 auto;position:relative;height:100%}

/* top bar */
.topbar{height:42px;background:var(--red)}
.social-strip{position:absolute;left:78px;top:0;display:flex;height:42px}
.social-strip span{width:42px;height:42px;border-right:1px solid rgba(255,255,255,.3);display:flex;align-items:center;justify-content:center}
.social-strip span:first-child{border-left:1px solid rgba(255,255,255,.3)}
.social-strip i{width:12px;height:12px;border-radius:50%;background:var(--white);display:block}
.contact-strip{position:absolute;right:78px;top:0;height:42px;display:flex;align-items:center;gap:34px;color:var(--white);font-size:14px}
.contact-strip div{display:flex;align-items:center;gap:10px}

/* header */
.site-header{height:84px;background:var(--white);box-shadow:0 2px 4px rgba(0,0,0,.08)}
.logo{position:absolute;left:78px;top:18px;font-family:var(--head);font-weight:700;font-size:40px;color:var(--ink);letter-spacing:-.5px}
.main-nav{position:absolute;right:78px;top:0;height:84px;display:flex;align-items:center;gap:40px;font-size:15px;color:var(--charcoal);text-transform:uppercase}
.main-nav .active{color:var(--red);display:flex;align-items:center;gap:10px}

/* hero */
.hero{height:551px;color:var(--white);text-align:center}
.hero-photo{position:absolute;inset:0;background:linear-gradient(180deg,#8f959b 0%,#6d737a 35%,#3b3f45 75%,#2a2c30 100%)}
.hero-shade{position:absolute;inset:0;background:rgba(20,22,26,.35)}
.hero h1{position:absolute;top:150px;left:0;right:0;font-family:var(--head);font-weight:700;font-size:50px;line-height:62px;text-transform:uppercase}
.hero p{position:absolute;top:282px;left:220px;right:220px;font-size:17px;line-height:29px;font-weight:600}
.btn{display:inline-block;font-family:var(--head);font-weight:700;text-transform:uppercase;text-align:center}
.btn-red{background:var(--red);color:var(--white)}
.hero .btn{position:absolute;top:362px;left:495px;width:210px;height:54px;line-height:54px;font-size:20px;border-radius:3px}
.slider-arrow{position:absolute;top:250px;width:46px;height:46px;border-radius:50%;background:rgba(0,0,0,.45);display:flex;align-items:center;justify-content:center}
.slider-arrow.prev{left:16px}.slider-arrow.next{right:16px}

/* welcome */
.welcome{height:328px;text-align:center}
.section-title{font-family:var(--head);font-weight:700;font-size:40px;color:var(--ink)}
.welcome .section-title{position:absolute;top:54px;left:0;right:0}
.welcome p{position:absolute;top:120px;left:185px;right:185px;font-size:13px;line-height:27px}
.scroll-cue{position:absolute;top:216px;left:574px;width:52px;height:52px;border:2px solid var(--red);border-radius:50%;display:flex;align-items:center;justify-content:center}

/* service boxes */
.service-boxes{height:468px;display:flex}
.service-box{width:600px;height:468px;position:relative;text-align:center;color:var(--white)}
.service-box.support{background:var(--red)}
.service-box.security{background:#343434}
.service-box svg{position:absolute;top:60px;left:252px}
.service-box h2{position:absolute;top:182px;left:0;right:0;font-family:var(--head);font-weight:600;font-size:46px}
.service-box p{position:absolute;top:255px;left:120px;right:120px;font-size:13px;line-height:27px}
.service-box .btn{position:absolute;top:352px;left:226px;width:126px;height:52px;line-height:50px;font-family:var(--body);font-weight:400;font-size:19px;border-radius:3px}
.btn-outline{border:2px solid rgba(255,255,255,.8);color:var(--white)}
.security .btn{background:var(--red);border:2px solid var(--red)}

/* about */
.about{height:505px;background:linear-gradient(90deg,#ffffff 0%,#f3f5f7 55%,#e5e9ee 100%)}
.about-photo{position:absolute;right:75px;top:0;width:470px;height:505px;background:linear-gradient(180deg,#d9dee4 0%,#9ea6ae 45%,#2f3a42 100%)}
.eyebrow{position:absolute;left:78px;top:76px;font-family:var(--head);font-weight:700;font-size:16px;color:var(--red);text-transform:uppercase}
.about h2{position:absolute;left:78px;top:100px;font-family:var(--head);font-weight:700;font-size:46px;color:var(--ink)}
.about .copy{position:absolute;left:78px;top:165px;width:540px;font-size:13px;line-height:27px}
.about .copy p+p{margin-top:16px}
.about .btn{position:absolute;left:78px;top:390px;width:186px;height:52px;line-height:52px;font-size:19px;border-radius:3px}

/* testimonials */
.testimonials{height:495px;text-align:center;color:var(--white)}
.testimonials-bg{position:absolute;inset:0;background:linear-gradient(180deg,#1e2024 0%,#2a2d32 60%,#1b1c1f 100%)}
.testimonials .section-title{position:absolute;top:55px;left:0;right:0;color:var(--white)}
.quote-mark{position:absolute;top:130px;left:561px;width:78px;height:78px;border:3px solid var(--red);border-radius:50%;display:flex;align-items:center;justify-content:center}
.testimonials blockquote{position:absolute;top:240px;left:220px;right:220px;font-size:14px;line-height:28px}
.client-name{position:absolute;top:332px;left:0;right:0;font-size:12px;font-weight:700;color:var(--red);text-transform:uppercase;letter-spacing:.5px}
.clients{position:absolute;top:366px;left:492px;display:flex;gap:18px;align-items:center}
.clients span{width:62px;height:62px;border-radius:50%;background:linear-gradient(180deg,#8a8e93,#55595e);border:3px solid rgba(255,255,255,.7)}
.clients span.current{width:68px;height:68px;background:linear-gradient(180deg,#c9ced4,#7d848c);border-color:var(--white)}
.clients-arrow{position:absolute;top:384px}
.clients-arrow.prev{left:445px}.clients-arrow.next{left:742px}

/* partners */
.partners{height:218px;background:var(--white)}
.partner-row{position:absolute;top:58px;left:100px;right:100px;display:flex;justify-content:space-between;align-items:center}
.partner{height:60px;background:#b3b3b3;border-radius:4px}
.partner.a{width:128px}.partner.b{width:160px;border-radius:30px}.partner.c{width:110px}.partner.d{width:150px}.partner.e{width:148px}
.dots{position:absolute;top:150px;left:546px;display:flex;gap:10px}
.dots i{width:26px;height:4px;background:var(--charcoal);display:block}
.dots i:last-child{background:var(--red)}

/* blog */
.blog{height:470px}
.blog-bg{position:absolute;inset:0;background:linear-gradient(180deg,#f4f1ef 0%,#d8d4d1 55%,#bdb8b4 100%)}
.blog .section-title{position:absolute;top:60px;left:0;right:0;text-align:center}
.post{position:absolute;top:148px;width:512px;height:254px;background:var(--white);display:flex;box-shadow:0 2px 8px rgba(0,0,0,.12)}
.post.one{left:78px}.post.two{left:610px}
.post-photo{width:230px;height:254px;flex:none}
.one .post-photo{background:linear-gradient(135deg,#0b3e56 0%,#1a6f8a 50%,#5fd3e8 100%)}
.two .post-photo{background:linear-gradient(135deg,#0f1b2e 0%,#27426a 55%,#5c7fb0 100%)}
.post-body{padding:28px 22px 0 22px}
.post h3{font-family:var(--body);font-weight:700;font-size:15px;line-height:25px;color:var(--ink)}
.post p{margin-top:12px;font-size:12px;line-height:25px}
.read-more{margin-top:12px;display:flex;align-items:center;gap:6px;font-size:12px;font-weight:700;color:var(--red);text-decoration:underline}

/* footer */
.site-footer{height:281px;background:var(--footer);color:#cfcfcf}
.footer-col{position:absolute;top:38px}
.footer-col h4{font-family:var(--body);font-weight:700;font-size:16px;color:var(--white);text-transform:uppercase;margin-bottom:24px}
.col-contact{left:78px;width:260px}
.col-sitemap{left:350px}.col-services{left:605px}
.contact-item{display:flex;gap:16px;font-size:12px;line-height:20px;margin-bottom:22px}
.contact-item svg{flex:none;margin-top:2px}
.contact-item strong{display:block;color:var(--red);font-weight:400;font-size:14px}
.footer-col ul{list-style:none}
.footer-col li{font-size:12px;margin-bottom:19px;display:flex;align-items:center;gap:12px}
.footer-col li::before{content:"";width:4px;height:4px;background:var(--red);border-radius:50%}
.footer-logo{position:absolute;right:78px;top:38px;font-family:var(--head);font-weight:700;font-size:40px;color:var(--red)}
.footer-social{position:absolute;right:78px;top:110px;display:flex;gap:12px}
.footer-social span{width:40px;height:40px;border-radius:50%;border:2px solid #666}
.footer-social span:first-child{background:var(--red);border-color:var(--red)}
.copyright{position:absolute;right:78px;top:170px;text-align:right;font-size:12px;line-height:24px}
.to-top{position:absolute;left:576px;bottom:0;width:0;height:0;border-left:24px solid transparent;border-right:24px solid transparent;border-bottom:16px solid #3c3c3c}
</style>
</head>
<body>

<div class="topbar">
  <div class="social-strip" aria-label="Social links"><span><i></i></span><span><i></i></span><span><i></i></span></div>
  <div class="contact-strip">
    <div><svg width="15" height="15" viewBox="0 0 24 24"><path fill="#fff" d="M6.6 10.8a15.2 15.2 0 0 0 6.6 6.6l2.2-2.2c.3-.3.7-.4 1-.2 1.1.4 2.3.6 3.6.6.6 0 1 .4 1 1V20c0 .6-.4 1-1 1C10.6 21 3 13.4 3 4c0-.6.4-1 1-1h3.5c.6 0 1 .4 1 1 0 1.3.2 2.5.6 3.6.1.3 0 .7-.2 1z"/></svg>123 456 7890</div>
    <div><svg width="16" height="13" viewBox="0 0 24 18"><path fill="#fff" d="M2 0h20a2 2 0 0 1 2 2v14a2 2 0 0 1-2 2H2a2 2 0 0 1-2-2V2a2 2 0 0 1 2-2zm0 3v.5l10 6.5 10-6.5V3L12 9z"/></svg>info@zorvanlumet.com</div>
  </div>
</div>

<header class="site-header">
  <div class="logo">Zorvan Lumet</div>
  <nav class="main-nav">
    <span class="active">Home <svg width="12" height="8" viewBox="0 0 12 8"><path d="M0 0h12L6 8z" fill="#a8151c"/></svg></span>
    <span>About Us</span><span>Services</span><span>Contact Us</span>
    <svg width="17" height="17" viewBox="0 0 20 20"><circle cx="8" cy="8" r="6" fill="none" stroke="#1c1c1c" stroke-width="3"/><path d="M12.5 12.5l6 6" stroke="#1c1c1c" stroke-width="3"/></svg>
  </nav>
</header>

<section class="hero">
  <div class="hero-photo" role="img" aria-label="London street with a clock tower and people walking, muted evening tones"></div>
  <div class="hero-shade"></div>
  <h1>IT Support and IT Security<br>Company</h1>
  <p>Lorem Ipsum is simply dummy text of the printing and typesetting psum has been the industry's standard Lorem Ipsum is simply dummy text of the printing.</p>
  <a class="btn btn-red">Contact Us</a>
  <span class="slider-arrow prev"><svg width="12" height="18" viewBox="0 0 12 18"><path d="M10 2L3 9l7 7" fill="none" stroke="#fff" stroke-width="2.5"/></svg></span>
  <span class="slider-arrow next"><svg width="12" height="18" viewBox="0 0 12 18"><path d="M2 2l7 7-7 7" fill="none" stroke="#fff" stroke-width="2.5"/></svg></span>
</section>

<section class="welcome">
  <h2 class="section-title">Welcome To Zorvan Lumet</h2>
  <p>Lorem Ipsum is simply dummy text of the printing and typesetting industry. Lorem Ipsum has been the industry's standard dummy text ever since the when an unknown printer took a galley of type and sZorvan Lumet scrambled it to make a type specimen book. It has survived not only five centuries, but also the leap into electronic.</p>
  <span class="scroll-cue"><svg width="20" height="20" viewBox="0 0 20 20"><path d="M4 4l6 6 6-6M4 10l6 6 6-6" fill="none" stroke="#a8151c" stroke-width="2"/></svg></span>
</section>

<section class="service-boxes">
  <div class="service-box support">
    <svg width="96" height="100" viewBox="0 0 96 100"><circle cx="44" cy="34" r="18" fill="#fff"/><path d="M22 34a22 22 0 0 1 44 0" fill="none" stroke="#fff" stroke-width="5"/><rect x="16" y="30" width="8" height="16" rx="3" fill="#fff"/><rect x="64" y="30" width="8" height="16" rx="3" fill="#fff"/><path d="M10 96c0-22 14-36 34-36s34 14 34 36z" fill="#fff"/><circle cx="76" cy="76" r="16" fill="#fff" stroke="#a8151c" stroke-width="3"/><path d="M71 72a5 5 0 1 1 6 5v4" fill="none" stroke="#a8151c" stroke-width="3"/><circle cx="77" cy="86" r="2" fill="#a8151c"/></svg>
    <h2>It Support</h2>
    <p>Lorem Ipsum is simply dummy text of the printing and typesetting industry. Lorem Ipsum has been the industry's standard Lorem Ipsum is simply.</p>
    <a class="btn btn-outline">More</a>
  </div>
  <div class="service-box security">
    <svg width="96" height="100" viewBox="0 0 96 100"><circle cx="38" cy="42" r="32" fill="none" stroke="#fff" stroke-width="4"/><ellipse cx="38" cy="42" rx="14" ry="32" fill="none" stroke="#fff" stroke-width="4"/><path d="M6 42h64M12 26h52M12 58h52" stroke="#fff" stroke-width="4"/><path d="M62 46l26 8v16c0 14-12 22-26 28-14-6-26-14-26-28V54z" fill="#343434" stroke="#fff" stroke-width="4"/></svg>
    <h2>It Security</h2>
    <p>Lorem Ipsum is simply dummy text of the printing and typesetting industry. Lorem Ipsum has been the industry's standard Lorem Ipsum is simply.</p>
    <a class="btn">More</a>
  </div>
</section>

<section class="about">
  <div class="about-photo" role="img" aria-label="Smiling IT professional holding a laptop and pointing forward"></div>
  <div class="eyebrow">About Us</div>
  <h2>Zorvan Lumet</h2>
  <div class="copy">
    <p>Lorem Ipsum is simply dummy text of the printing and typesetting industry. Lorem Ipsum has been the industry's standard dummy text ever since the when an unknown printer took of type and sZorvan Lumet scrambled.</p>
    <p>Lorem Ipsum is simply dummy text of the printing and typesetting industry. Lorem Ipsum has been the industry's standard dummy text ever since the when an unknown printer took a galley of type and sZorvan Lumet scrambled it to make a it has survived not only five centuries, but also the leap into electronic.</p>
  </div>
  <a class="btn btn-red">Learn More</a>
</section>

<section class="testimonials">
  <div class="testimonials-bg" role="img" aria-label="Dark background photo of a person working at a computer"></div>
  <h2 class="section-title">Happy Clients</h2>
  <span class="quote-mark"><svg width="30" height="24" viewBox="0 0 30 24"><path d="M2 24V12L8 0h5L9 12h4v12zM17 24V12L23 0h5l-4 12h4v12z" fill="#a8151c"/></svg></span>
  <blockquote>"Lorem Ipsum is simply dummy text of the printing and typesetting industry. Lorem Ipsum has been the industry's standard dummy text ever since the 1500s, when an unknown printer took a galley of type and scrambled it to make a type specimen book it has survived not only. "</blockquote>
  <div class="client-name">Clients Name</div>
  <svg class="clients-arrow prev" width="14" height="26" viewBox="0 0 14 26"><path d="M12 2L2 13l10 11" fill="none" stroke="#9a9a9a" stroke-width="2"/></svg>
  <div class="clients" aria-label="Client portraits">
    <span role="img" aria-label="Client portrait"></span>
    <span class="current" role="img" aria-label="Client portrait"></span>
    <span role="img" aria-label="Client portrait"></span>
  </div>
  <svg class="clients-arrow next" width="14" height="26" viewBox="0 0 14 26"><path d="M2 2l10 11L2 24" fill="none" stroke="#9a9a9a" stroke-width="2"/></svg>
</section>

<section class="partners">
  <div class="partner-row" aria-label="Partner badges">
    <span class="partner a"></span><span class="partner b"></span><span class="partner c"></span><span class="partner d"></span><span class="partner e"></span>
  </div>
  <div class="dots"><i></i><i></i><i></i></div>
</section>

<section class="blog">
  <div class="blog-bg" role="img" aria-label="Soft background photo of hands typing on a laptop"></div>
  <h2 class="section-title">Latest Blog Post</h2>
  <article class="post one">
    <div class="post-photo" role="img" aria-label="Person with glasses lit by blue screen light"></div>
    <div class="post-body">
      <h3>Lorem Ipsum is the no simply Dummy text of the printing.</h3>
      <p>Lorem Ipsum is the simply dummy text of the printi ng and typesetting industry. Lorem Ipsum has the been the print text of print industry.</p>
      <div class="read-more">Read More... <svg width="10" height="10" viewBox="0 0 10 10"><path d="M1 1l4 4-4 4M5 1l4 4-4 4" fill="none" stroke="#a8151c" stroke-width="1.6"/></svg></div>
    </div>
  </article>
  <article class="post two">
    <div class="post-photo" role="img" aria-label="Technician seated among server racks in a data centre"></div>
    <div class="post-body">
      <h3>Lorem Ipsum is the no simply Dummy text of the printing.</h3>
      <p>Lorem Ipsum is the simply dummy text of the printi ng and typesetting industry. Lorem Ipsum has the been the print text of print industry.</p>
      <div class="read-more">Read More... <svg width="10" height="10" viewBox="0 0 10 10"><path d="M1 1l4 4-4 4M5 1l4 4-4 4" fill="none" stroke="#a8151c" stroke-width="1.6"/></svg></div>
    </div>
  </article>
</section>

<footer class="site-footer">
  <div class="footer-col col-contact">
    <h4>Contact Us</h4>
    <div class="contact-item"><svg width="16" height="18" viewBox="0 0 16 18"><path d="M1 3h14M1 9h14M1 15h14" stroke="#a8151c" stroke-width="3"/></svg><div><strong>Zorvan Lumet</strong>101 - Lorem ipsum is simple text of print and type setting.</div></div>
    <div class="contact-item"><svg width="16" height="16" viewBox="0 0 24 24"><path fill="#a8151c" d="M6.6 10.8a15.2 15.2 0 0 0 6.6 6.6l2.2-2.2c.3-.3.7-.4 1-.2 1.1.4 2.3.6 3.6.6.6 0 1 .4 1 1V20c0 .6-.4 1-1 1C10.6 21 3 13.4 3 4c0-.6.4-1 1-1h3.5c.6 0 1 .4 1 1 0 1.3.2 2.5.6 3.6.1.3 0 .7-.2 1z"/></svg><div>123 456 7890</div></div>
    <div class="contact-item"><svg width="16" height="13" viewBox="0 0 24 18"><path fill="#a8151c" d="M2 0h20a2 2 0 0 1 2 2v14a2 2 0 0 1-2 2H2a2 2 0 0 1-2-2V2a2 2 0 0 1 2-2zm0 3v.5l10 6.5 10-6.5V3L12 9z"/></svg><div>info@zorvanlumet.com</div></div>
  </div>
  <div class="footer-col col-sitemap">
    <h4>Sitemap</h4>
    <ul><li>Home</li><li>About Us</li><li>Services</li><li>Contact Us</li></ul>
  </div>
  <div class="footer-col col-services">
    <h4>Services</h4>
    <ul><li>It Support</li><li>It Security</li></ul>
  </div>
  <div class="footer-logo">Zorvan Lumet</div>
  <div class="footer-social" aria-label="Social links"><span></span><span></span><span></span></div>
  <div class="copyright">©Zorvan Lumet - 2018 All Right<br>Reserved.</div>
  <span class="to-top"></span>
</footer>

</body>
</html>
```